Blogging Platform for Christian Missions

We need the main (one) page design for FaithTrailer. FaithTrailer is a blogging platform for people (missionaries) who work for Christian Mission organisations in various countries. It will provides an easy way for them to setup and maintain a blog that will have features specifically for missions.

There's a lot of work involved in creating a web page design so I am happy to receive many quick rough designs. I will select my favourite four or five designs and these can submit the full design.

Please see the attached wireframe. Please also see the attached logo.

Main colours
- black
- white
- grey
- red (see logo colour) can be used occasionally eg. titles
- another complementary colour - occasionally used

Photos uploaded by the missionaries will provide colour for the website.

It needs to be a clean design that is not cluttered. The main focus are the blog posts. The information on the side complements the blog. There are navigational options at the top and bottom. The FaithTrailer logo is not the main focus. The person's name (blog owner) is what needs to be most prominent.

I love the BrightKarnu design (http://www.brightkarnu.com/). I particularly like the soft design - light grey background, white background boxes for content. The focus is the content - text and photos. I also like the subtle use of breakout image - "Step into the Venture". I like the black navigation header and the black footer. I do not want a exact copy of the site but I'd like to use this concept .

I also like this Vexlo design (http://calm.vexlo.com/theme/preview/5194) because of the white box (and the shadow) for the content. I also like how the word "Quote" and the number of "notes" breaks out of the white content area (see attachment). I'd like to do this, if possible with the date. This is just a "nice to have" - definitely not essential. I don't like the font for the title in this example.

We have build a simple prototype already. I cautiously show this because I want the the design of this to be completely ignored. I used a free template. Along with the wireframe this prototype should an idea of what kind of content will be displayed but please don't look too much at it.
http://faithtrailer.org/blog/1

The design will be used to create a website using Plonkit. We will use zScriptor so feel free to suggest an animation or lightbox effect to make your design more dynamic. This is a nice to have.

Once we have our final design we will need to define the style for:
- h1 through h4 tags
- Paragraphs
- Lists
- Block quotes
- Italics, bolding and underlining
- Links, including active, hover and visited states

Please let me know what additional information you need. Also let me know if there is something I have not considered.

Target Market(s)

The target customers are mission workers aged 25-35 who will post blog entries. These posts will be read by their friends and family.

Industry/Entity Type

Build

Requirements
Must have
• Clean simple design. Must be inspired by the BrightKarnu (http://www.brightkarnu.com/) design without copying it.
Nice to have
• Design element that breaks out of the boxes. See the screenshot attached from the Vexlo site. Described more in the project overview.
Should not have
• Should not use fonts that are not web-friendly. Should not have features that will be difficult to implement using HTML/CSS.

```html
<!DOCTYPE html>
<html lang="en">
<head>
<meta charset="utf-8">
<title>Hannah Doyle – FaithTrailer</title>
<link href="https://fonts.googleapis.com/css2?family=Arimo:wght@400;700&family=Tinos:ital@1&display=swap" rel="stylesheet">
<style>
:root{
  --black:#2b2b2b;
  --nav-text:#ffffff;
  --red:#e0102f;
  --page:#ececec;
  --side:#efefef;
  --white:#ffffff;
  --ink:#333333;
  --muted:#8a8a8a;
  --heading:#8f8f8f;
  --line:#d9d9d9;
  --bar:#e6e6e6;
  --footer:#262626;
}
*{box-sizing:border-box;margin:0;padding:0}
html,body{width:930px;height:1200px;overflow:hidden}
body{background:var(--page);font-family:"Arimo",Arial,sans-serif;color:var(--ink);position:relative}
a{color:inherit;text-decoration:none}

.topnav{position:absolute;top:0;left:0;width:930px;height:28px;background:var(--black);display:flex;align-items:center;font-size:11px;font-weight:700;color:var(--nav-text);text-transform:uppercase}
.topnav .mark{width:26px;height:26px;margin:0 22px 0 55px;display:flex;align-items:center;justify-content:center}
.topnav .mark span{width:12px;height:12px;border-radius:50%;border:2px solid #fff}
.topnav .item{height:28px;line-height:28px;padding:0 10px}
.topnav .item.active{background:var(--red)}
.topnav .account{margin-left:auto;margin-right:55px;display:flex;gap:10px}

.masthead{position:absolute;top:28px;left:0;width:930px;height:108px;background:var(--white);border-bottom:1px solid var(--line)}
.masthead h1{position:absolute;left:64px;top:32px;font-size:30px;font-weight:700;color:var(--heading)}
.masthead .org{position:absolute;left:65px;top:70px;font-size:15px;color:var(--heading)}
.search{position:absolute;left:658px;top:45px;width:208px;height:24px;border:1px solid #e3e3e3;background:#fafafa}
.search svg{position:absolute;right:6px;top:5px}

.post{position:absolute;left:62px;width:531px;background:var(--white);box-shadow:0 1px 4px rgba(0,0,0,.18)}
.date{position:absolute;left:-40px;top:18px;width:53px;height:58px;background:var(--red);color:#fff;text-align:center}
.date b{display:block;font-size:22px;font-weight:400;line-height:28px;margin-top:6px}
.date span{font-size:13px}
.post h2{font-size:20px;font-weight:400;color:var(--heading);margin:20px 28px 0;padding-bottom:10px;border-bottom:1px solid var(--line)}
.share{position:absolute;right:28px;top:18px;display:flex;gap:3px}
.share i{width:22px;height:22px;display:block;border-radius:3px}
.share .a{background:#3b5b98}.share .b{background:#4fb0db}
.post p{font-size:10px;line-height:20.8px;margin:6px 28px 0;text-align:justify}
.post p + p{margin-top:20px}
.photo{display:block;margin:18px 30px 0;width:468px;height:256px;border:4px solid #d4d4d4;background:linear-gradient(160deg,#4b5f86 0%,#3d3f26 35%,#8a4a2c 60%,#2f2a1a 100%)}
.postbar{display:flex;justify-content:space-between;align-items:center;margin:20px 20px 0;height:21px;background:var(--bar);padding:0 14px 0 10px;font-family:"Tinos",Georgia,serif;font-style:italic;font-size:11px;color:var(--muted)}
.postbar .c{display:flex;align-items:center;gap:8px}
.postbar .more{color:#b03a48}
.post.one{top:155px;height:563px}
.post.two{top:735px;height:226px}
.post.two .postbar{margin-top:12px}

.pager{position:absolute;top:981px;left:166px;display:flex;gap:10px;font-size:10px;color:#b5b5b5}
.pager a{height:26px;line-height:26px;text-align:center;background:var(--white);border:1px solid #e2e2e2;width:30px}
.pager a.wide{width:60px}
.pager a.on{background:var(--red);color:#fff;border-color:var(--red)}

.sidebar{position:absolute;left:633px;top:137px;width:255px;height:927px;background:var(--side);border-left:1px solid #e2e2e2;border-right:1px solid #e2e2e2}
.follow{margin:10px 0 0 27px;width:205px;height:31px;background:var(--white);border:1px solid #dcdcdc;display:flex;align-items:center;font-size:15px;color:#555;position:relative}
.follow .sq{width:26px;height:26px;margin:0 8px 0 2px;border-radius:3px}
.follow .plus{width:20px;height:20px;margin:0 12px 0 10px;border-radius:50%;border:1px solid #ddd;color:var(--red);font-size:18px;line-height:18px;text-align:center}
.follow .count{position:absolute;right:22px;font-family:"Tinos",Georgia,serif;font-style:italic;color:#bbb;font-size:17px}
.follow + .follow{margin-top:10px}
.widget{border-top:1px solid #dcdcdc;padding:8px 12px 0 12px}
.widget h3{font-size:15px;font-weight:400;color:var(--heading);padding-bottom:7px;border-bottom:1px solid #dcdcdc;margin-bottom:8px}
.widget p,.widget li{font-size:10px;line-height:14px;color:var(--ink)}
.widget .link{display:block;font-size:10px;color:#b0b0b0;text-decoration:underline;margin-top:8px;padding-bottom:4px}
.about{height:154px;margin-top:16px}
.about .row{display:flex;gap:8px}
.about .pic{flex:0 0 104px;height:80px;background:#555;border:3px solid #d7d7d7}
.about .row p{text-align:justify}
.ministry{height:155px}
.ministry p{text-align:justify}
.malawi{height:222px}
.map{display:block;margin:0 8px 6px;width:214px;height:100px;border:3px solid #d7d7d7;background:linear-gradient(135deg,#e8e4d8,#d9d6ca)}
.events{height:103px}
.events2{height:146px}
.events2 ul{padding-left:10px}

.footer{position:absolute;left:0;top:1064px;width:930px;height:136px;background:var(--footer);color:#fff}
.fcol{position:absolute;top:16px;font-size:10px;line-height:14px}
.fcol h4{font-size:10px;font-weight:700;margin-bottom:12px}
.fcol.c1{left:58px}.fcol.c2{left:206px}.fcol.c3{left:378px}
.flogo{position:absolute;left:646px;top:55px;display:flex;align-items:center;gap:8px;font-size:22px;color:#fff}
.flogo span{width:30px;height:30px;border:3px solid #fff;border-radius:50%}
</style>
</head>
<body>

<nav class="topnav">
  <div class="mark"><span></span></div>
  <a class="item active" href="#">Mission Blogs</a>
  <a class="item" href="#">Opportunities</a>
  <a class="item" href="#">Option3</a>
  <a class="item" href="#">Option4</a>
  <div class="account"><a href="#">Sign in</a><span>|</span><a href="#">Register</a></div>
</nav>

<header class="masthead">
  <h1>Hannah Doyle</h1>
  <div class="org">GMN Australia</div>
  <div class="search">
    <svg width="13" height="13" viewBox="0 0 13 13"><circle cx="5" cy="5" r="4" fill="none" stroke="#777" stroke-width="1.6"/><line x1="8" y1="8" x2="12" y2="12" stroke="#777" stroke-width="1.8"/></svg>
  </div>
</header>

<article class="post one">
  <div class="date"><b>01</b><span>July</span></div>
  <div class="share"><i class="a"></i><i class="b"></i></div>
  <h2>Just Arrived</h2>
  <p>Lorem ipsum dolor sit amet, consectetuer adipiscing elit. Aenean commodo ligula eget dolor. Aenean massa. Cum sociis natoque penatibus et magnis dis parturient montes, nascetur ridiculus mu. Donec quam felis, ultricies nec, pellentesque eu, pretium quis, sem. Nulla consequat massa quisburitjusto. Nullam dictum felis eu pede mollis pretium. Integer tincidunt. Cras dapibus.</p>
  <p>Enim. Aliquam lorem ante, dapibus in, viverra quis, feugiat a, tellus. Phasellus viverra nulla ut metus varius laoreet. Quisque rutrum. bus in, viverra quis, feugiat a, tellus. Phasellus viverra nulla ut metus varius laoreet. Quisque rutrum. Aenean imperdiet. Etiam ultricies nisi vel augue. Curabitur ullamcorper ultricies nisi. Nam eget dui. Etiam rhoncus. Maecenas tempus, tellus eget condimentum</p>
  <div class="photo" role="img" aria-label="Photo of a red brick mission house among trees under a blue sky"></div>
  <div class="postbar">
    <span class="c"><svg width="11" height="9" viewBox="0 0 11 9"><path d="M1 1h9v5H4L2 8V6H1z" fill="#e0102f"/></svg>4 comments</span>
    <a class="more" href="#">Read more</a>
  </div>
</article>

<article class="post two">
  <div class="date"><b>01</b><span>July</span></div>
  <div class="share"><i class="a"></i><i class="b"></i></div>
  <h2>Only 14 days to go before I fly for Malawi</h2>
  <p>Lorem ipsum dolor sit amet, consectetuer adipiscing elit. Aenean commodo ligula eget dolor. Aenean massa. Cum sociis natoque penatibus et magnis dis parturient montes, nascetur ridiculus mus. Donec quum dolor sit amet, consectetuer adipiscing elit. Aenean commodo ligula eget dolor. Aenean massa. Cum felis, ultricies nec, pellentesque eu, pretium quis, sem. Nulla consequat massa quis enim.Enim. Aliquam lorem ante, dapibus in, viverra quis, feugiat a, tell Nulla consequat massa quis enim.Enim. Aliquam lorem ante, dapibus in, viverra quis, feugiat a, tellus. vel augue</p>
  <div class="postbar">
    <span class="c"><svg width="11" height="9" viewBox="0 0 11 9"><path d="M1 1h9v5H4L2 8V6H1z" fill="#e0102f"/></svg>4 comments</span>
    <a class="more" href="#">Read more</a>
  </div>
</article>

<nav class="pager">
  <a class="wide" href="#">Previous</a>
  <a class="on" href="#">1</a><a href="#">2</a><a href="#">3</a><a href="#">4</a><a href="#">5</a>
  <a class="wide" href="#">Next</a>
</nav>

<aside class="sidebar">
  <div class="follow"><span class="plus">+</span>Follow Hannah Doyle</div>
  <div class="follow"><span class="sq" style="background:#3b5b98"></span>Find us on<span class="count">134</span></div>
  <div class="follow"><span class="sq" style="background:#4fb0db"></span>Follow us on<span class="count">134</span></div>

  <section class="widget about">
    <h3>About Hannah</h3>
    <div class="row">
      <div class="pic" role="img" aria-label="Profile photo of Hannah"></div>
      <p>Lorem ipsum dolor sit amet, consectetuer adipiscing elit. Aenean commodo ligula eget dolor. Aenean</p>
    </div>
    <a class="link" href="#">View my complete profile</a>
  </section>

  <section class="widget ministry">
    <h3>About Hannah's Ministry</h3>
    <p>Lorem ipsum dolor sit amet, consectetuer adipiscing elit. Aenean commodo ligula eget dolor. Aenean Lorem ipsum dolor sit amet, consectetuer adipiscing elit. Aenean commodo ligula eget dolor. Aenea Lorem ipsum</p>
    <a class="link" href="#">Read more</a>
  </section>

  <section class="widget malawi">
    <h3>About Malawi</h3>
    <div class="map" role="img" aria-label="Street map of the area in Malawi with a location pin"></div>
    <p>Lorem ipsum dolor sit amet, consectetuer adipiscing elit. Aenean commodo ligula eget dolor. Aenean Lorem</p>
    <a class="link" href="#">Read more</a>
  </section>

  <section class="widget events">
    <h3>GMN Events</h3>
    <p>GMN Prayer Event - May 15th<br>GMN Conference - June 30th</p>
    <a class="link" href="#">Read more</a>
  </section>

  <section class="widget events2">
    <h3>GMN Events</h3>
    <ul>
      <li>Teacher in Blanta (2yrs)</li>
      <li>Financial Controller (long term)</li>
      <li>Project Manager (6months+)</li>
      <li>Bible College Lecturer (long term)</li>
    </ul>
    <a class="link" href="#">Read more</a>
  </section>
</aside>

<footer class="footer">
  <div class="fcol c1"><h4>About Us</h4>About FaithTrailer<br>Missionaries<br>Mission Agencies<br>Churches<br>Mission Supporters<br>Privacy</div>
  <div class="fcol c2"><h4>Regions Mission</h4>Africa<br>Asia<br>North America<br>Latin America<br>Aust/Pacific</div>
  <div class="fcol c3"><h4>Agencies</h4>CRV<br>Global Outreach Link<br>GMN Australia<br>WRV</div>
  <div class="flogo"><span></span>faithtrailer.org</div>
</footer>

</body>
</html>
```